New corporate stationery design for UK train leasing company

In advance of an office move later this year we are looking to redesign all our corporate stationery (business cards, letterhead, compliment slips, envelopes etc) as well as small branded items (such as mouse mats, drink mats, etc).

We wish to keep the same logo and corporate colours but are looking for a modern, fresh look that will tie in our stationery more with the look of our website and our PowerPoint template. We have a strapline, "Rail People, Real Expertise" that we would like to incorporate into the stationery design and also need to include a "TOVEC" logo on the bottom of the letterhead/compliment slips. We have two offices so will need letterhead and compliment slips with both addresses.

The files attached include different versions of our logo (the main one is the black with green halo, file 1 or 3), our brand guidelines summary (including Pantone colours), the TOVEC logo and PowerPoint template.

More information about the business can be found at www.copperlinefleet.co.uk.

If you have any questions please let me know.

I look forward to seeing the designs!
Regards
Harriet

Main audience are train operators, rail industry suppliers, passenger transport groups, government and other political organisations, financiers/lenders.

Business

```html
<!DOCTYPE html>
<html lang="en">
<head>
<meta charset="utf-8">
<title>Copperline Fleet – Corporate Stationery</title>
<link rel="stylesheet" href="https://fonts.googleapis.com/css2?family=Poppins:wght@300;400;500;600&display=swap">
<style>
  :root {
    --bg: #e3e5e8;
    --paper: #ffffff;
    --ink: #3c3d40;
    --ink-soft: #6b6d72;
    --ink-faint: #9a9ca1;
    --teal: #1fa198;
    --edge: #d4d6da;
    --shadow: rgba(40, 45, 55, 0.12);
  }
  * { box-sizing: border-box; margin: 0; padding: 0; }
  html, body { width: 1200px; height: 789px; overflow: hidden; }
  body {
    background: var(--bg);
    font-family: "Poppins", sans-serif;
    color: var(--ink);
    position: relative;
  }
  .sheet {
    position: absolute;
    background: var(--paper);
    box-shadow: 0 1px 0 var(--edge), 0 8px 22px var(--shadow);
  }

  /* brand name wordmark */
  .brand { display: flex; align-items: center; gap: 8px; }
  .brand-dot { width: 10px; height: 10px; border-radius: 50%; background: var(--teal); flex: none; }
  .brand-name { font-weight: 300; color: var(--ink-soft); letter-spacing: -0.5px; line-height: 1; }

  .icon { width: 12px; height: 12px; flex: none; fill: var(--teal); }
  .contact-row { display: flex; align-items: flex-start; gap: 7px; }
  .contact-text { font-size: 7px; line-height: 1.45; color: var(--ink-soft); }

  .web {
    font-size: 11px; font-weight: 500; letter-spacing: 5px; color: var(--ink);
  }

  /* letterhead */
  .letterhead { left: 48px; top: 36px; width: 508px; height: 718px; }
  .letterhead .contacts { position: absolute; right: 34px; top: 34px; display: flex; flex-direction: column; gap: 10px; }
  .letterhead .brand { position: absolute; left: 46px; top: 118px; }
  .letterhead .brand-name { font-size: 40px; }
  .letter { position: absolute; left: 46px; top: 196px; width: 400px; font-size: 7.2px; line-height: 1.6; color: var(--ink-soft); }
  .letter p { margin-bottom: 10px; }
  .letter .recipient { color: var(--ink); }
  .letter .recipient strong { font-weight: 600; }
  .signature { width: 64px; height: 30px; background: #eceef0; margin: 4px 0 6px; }
  .signer strong { font-weight: 600; color: var(--ink); }
  .letterhead .web { position: absolute; right: 34px; bottom: 30px; }

  /* compliment slip */
  .slip { left: 612px; top: 36px; width: 540px; height: 262px; }
  .slip .brand { position: absolute; left: 34px; top: 30px; }
  .slip .brand-name { font-size: 30px; }
  .slip .strapline { position: absolute; left: 52px; top: 70px; font-size: 7px; letter-spacing: 1px; color: var(--ink-faint); }
  .slip .web { position: absolute; left: 34px; bottom: 28px; }

  /* business cards */
  .card { width: 258px; height: 158px; top: 350px; }
  .card-front { left: 612px; }
  .card-back { left: 894px; }
  .card-front .brand { position: absolute; left: 20px; top: 20px; }
  .card-front .brand-name { font-size: 22px; }
  .card-front .details { position: absolute; left: 20px; top: 66px; display: flex; flex-direction: column; gap: 8px; }
  .person-name { font-size: 9px; font-weight: 600; color: var(--teal); letter-spacing: 1px; }
  .person-role { font-size: 6.5px; color: var(--ink-soft); }
  .card-back .brand { position: absolute; left: 50%; top: 50px; transform: translateX(-50%); }
  .card-back .brand-name { font-size: 28px; }
  .card-back .social { position: absolute; right: 18px; bottom: 16px; display: flex; gap: 12px; }
  .social-item { display: flex; align-items: center; gap: 4px; font-size: 6px; color: var(--ink-soft); }
  .social-mark { width: 8px; height: 8px; background: var(--teal); }
</style>
</head>
<body>

<svg width="0" height="0" style="position:absolute" aria-hidden="true">
  <symbol id="i-pin" viewBox="0 0 24 24"><path d="M12 2a7 7 0 0 0-7 7c0 5 7 13 7 13s7-8 7-13a7 7 0 0 0-7-7zm0 9.5A2.5 2.5 0 1 1 12 6.5a2.5 2.5 0 0 1 0 5z"/></symbol>
  <symbol id="i-phone" viewBox="0 0 24 24"><path d="M6.6 10.8a15 15 0 0 0 6.6 6.6l2.2-2.2a1 1 0 0 1 1-.25 11.4 11.4 0 0 0 3.6.57 1 1 0 0 1 1 1V20a1 1 0 0 1-1 1A17 17 0 0 1 3 4a1 1 0 0 1 1-1h3.5a1 1 0 0 1 1 1c0 1.25.2 2.45.57 3.57a1 1 0 0 1-.25 1z"/></symbol>
  <symbol id="i-person" viewBox="0 0 24 24"><circle cx="12" cy="8" r="4.5"/><path d="M3 21c0-4.5 4-7 9-7s9 2.5 9 7z"/></symbol>
</svg>

<!-- Letterhead -->
<section class="sheet letterhead">
  <div class="contacts">
    <div class="contact-row">
      <svg class="icon"><use href="#i-pin"/></svg>
      <p class="contact-text">Unit 4, Harbour Court<br>Leeds LS1 4DY, UK</p>
    </div>
    <div class="contact-row">
      <svg class="icon"><use href="#i-phone"/></svg>
      <p class="contact-text">+44 113 496 0218<br>info@copperlinefleet.co.uk</p>
    </div>
  </div>

  <div class="brand"><span class="brand-dot"></span><span class="brand-name">copperline fleet</span></div>

  <div class="letter">
    <p>July 2, 2019</p>
    <p class="recipient"><strong>Dear Sir,</strong><br>ABC Building, 4d St, Country Name</p>
    <p>Lorem Ipsum is simply dummy text of the printing and typesetting industry. Lorem Ipsum has been the industry's standard dummy text ever since the 1500s, when an unknown printer took a galley of type and scrambled it to make a type specimen book. It has survived not only five centuries, but also the leap into electronic typesetting, remaining essentially unchanged. It was popularised in the 1960s with the release of Letraset sheets containing Lorem Ipsum passages, and more recently with desktop publishing software like Aldus PageMaker including versions of Lorem Ipsum.</p>
    <p>Lorem Ipsum is simply dummy text of the printing and typesetting industry. Lorem Ipsum has been the industry's standard dummy text ever since the 1500s, when an unknown printer took a galley of type and scrambled it to make a type specimen book.</p>
    <p>Lorem Ipsum is simply dummy text of the printing and typesetting industry. Lorem Ipsum has been the industry's standard dummy text ever since the 1500s, when an unknown printer took a galley of type and scrambled it to make a type specimen book. It has survived not only five centuries, but also the leap into electronic typesetting, remaining essentially unchanged. It was popularised in the 1960s with the release of Letraset sheets containing Lorem Ipsum passages, and more recently with desktop publishing software like Aldus PageMaker including versions of Lorem Ipsum.</p>
    <p>Best Regards,</p>
    <div class="signature" role="img" aria-label="Handwritten signature"></div>
    <p class="signer"><strong>Daniel Hewitt</strong><br>Director<br>ABC Building, 4d St, Country Name</p>
  </div>

  <p class="web">www.copperlinefleet.co.uk</p>
</section>

<!-- Compliment slip -->
<section class="sheet slip">
  <div class="brand"><span class="brand-dot"></span><span class="brand-name">copperline fleet</span></div>
  <p class="strapline">Rail People, Real Expertise</p>
  <p class="web">www.copperlinefleet.co.uk</p>
</section>

<!-- Business card front -->
<section class="sheet card card-front">
  <div class="brand"><span class="brand-dot"></span><span class="brand-name">copperline fleet</span></div>
  <div class="details">
    <div class="contact-row">
      <svg class="icon"><use href="#i-person"/></svg>
      <div><p class="person-name">JOHN MERCER</p><p class="person-role">Fleet Manager</p></div>
    </div>
    <div class="contact-row">
      <svg class="icon"><use href="#i-pin"/></svg>
      <p class="contact-text">Unit 4, Harbour Court<br>Leeds LS1 4DY, UK</p>
    </div>
    <div class="contact-row">
      <svg class="icon"><use href="#i-phone"/></svg>
      <p class="contact-text">+44 113 496 0218<br>john@copperlinefleet.co.uk</p>
    </div>
  </div>
</section>

<!-- Business card back -->
<section class="sheet card card-back">
  <div class="brand"><span class="brand-dot"></span><span class="brand-name">copperline fleet</span></div>
  <div class="social">
    <span class="social-item"><span class="social-mark"></span>/copperlinefleet</span>
    <span class="social-item"><span class="social-mark"></span>/copperline</span>
  </div>
</section>

</body>
</html>
```